VOMRA Pty Ltd Business Card

Looking for a simple yet eye-catching double-sided business card design using my company logo on one side and contact details on the other.

Target Market(s)

Government

Industry/Entity Type

Communication Systems Engineering

Contact Information for Business Card

VOMRA Pty Ltd

Requirements
Nice to have
• Would be great to have a QR code so details can be scanned into contacts

```html
<!DOCTYPE html>
<html lang="en">
<head>
<meta charset="utf-8">
<title>VOMRA Pty Ltd Business Card</title>
<link href="https://fonts.googleapis.com/css2?family=Open+Sans:wght@400;600;700&display=swap" rel="stylesheet">
<style>
  :root {
    --backdrop: #222324;
    --slate: #36424b;
    --slate-line: #3f4c56;
    --paper: #ffffff;
    --ink: #1f2326;
  }
  * { box-sizing: border-box; margin: 0; padding: 0; }
  html, body { width: 1200px; height: 780px; overflow: hidden; }
  body {
    background: var(--backdrop);
    font-family: "Open Sans", Arial, sans-serif;
    position: relative;
  }
  .card {
    position: absolute;
    width: 560px;
    height: 320px;
    overflow: hidden;
  }
  /* Front side */
  .card-front {
    left: 140px;
    top: 50px;
    background: var(--slate);
    display: flex;
    align-items: center;
    justify-content: center;
    gap: 22px;
  }
  .brand-dot {
    width: 64px;
    height: 64px;
    border-radius: 50%;
    background: var(--slate-line);
  }
  .brand-name {
    font-weight: 700;
    font-size: 66px;
    letter-spacing: 2px;
    color: #2a343b;
  }
  /* Back side */
  .card-back {
    left: 500px;
    top: 410px;
    background: var(--paper);
  }
  .back-brand {
    position: absolute;
    left: 150px;
    top: 30px;
    display: flex;
    align-items: center;
    gap: 16px;
  }
  .back-brand .brand-dot { width: 52px; height: 52px; background: var(--slate); }
  .back-brand .brand-name { font-size: 50px; color: var(--slate); }
  .holder {
    position: absolute;
    right: 308px;
    top: 146px;
    text-align: right;
    color: var(--slate);
  }
  .holder-name { font-weight: 700; font-size: 26px; line-height: 1.1; }
  .holder-role { font-size: 15px; color: var(--ink); }
  .divider {
    position: absolute;
    left: 270px;
    top: 130px;
    width: 2px;
    height: 80px;
    background: var(--ink);
  }
  .contacts {
    position: absolute;
    left: 288px;
    top: 128px;
    list-style: none;
    color: var(--ink);
    font-size: 16px;
  }
  .contacts li { display: flex; align-items: center; gap: 9px; height: 26px; }
  .contacts svg { width: 15px; height: 15px; fill: var(--slate); }
  .band { position: absolute; left: 0; top: 0; width: 560px; height: 320px; }
  .address {
    position: absolute;
    left: 0;
    right: 0;
    bottom: 16px;
    text-align: center;
    color: var(--paper);
    font-size: 15px;
    letter-spacing: 0.3px;
  }
</style>
</head>
<body>
  <section class="card card-front" aria-label="Card front">
    <span class="brand-dot"></span>
    <span class="brand-name">VOMRA</span>
  </section>

  <section class="card card-back" aria-label="Card back">
    <svg class="band" viewBox="0 0 560 320" aria-hidden="true">
      <path d="M0 262 Q300 258 560 205" fill="none" stroke="var(--slate)" stroke-width="2"/>
      <path d="M0 274 Q310 268 560 220 L560 320 L0 320 Z" fill="var(--slate)"/>
    </svg>

    <div class="back-brand">
      <span class="brand-dot"></span>
      <span class="brand-name">VOMRA</span>
    </div>

    <div class="holder">
      <p class="holder-name">Jordan Hale</p>
      <p class="holder-role">Co-Founder</p>
    </div>

    <span class="divider"></span>

    <ul class="contacts">
      <li>
        <svg viewBox="0 0 24 24"><path d="M6.6 10.8a15 15 0 0 0 6.6 6.6l2.2-2.2c.3-.3.7-.4 1-.2 1.1.4 2.300.6 3.6.6.6 0 1 .4 1 1V20c0 .6-.4 1-1 1A17 17 0 0 1 3 4c0-.6.4-1 1-1h3.5c.6 0 1 .4 1 1 0 1.3.2 2.5.6 3.6.1.3 0 .7-.2 1z"/></svg>
        <span>(555) 014-2231</span>
      </li>
      <li>
        <svg viewBox="0 0 24 24"><path d="M12 2a10 10 0 1 0 0 20 10 10 0 0 0 0-20zm6.9 6h-2.9a15.7 15.7 0 0 0-1.4-3.6A8 8 0 0 1 18.9 8zM12 4c.8 1.2 1.5 2.5 1.900 4h-3.8c.4-1.5 1.1-2.8 1.9-4zM4.3 14a8 8 0 0 1 0-4h3.4a16 16 0 0 0 0 4zm.8 2H8c.3 1.3.8 2.5 1.4 3.6A8 8 0 0 1 5.1 16zM8 8H5.1a8 8 0 0 1 4.3-3.6C8.8 5.5 8.3 6.7 8 8zm4 12c-.8-1.2-1.5-2.5-1.9-4h3.8c-.4 1.5-1.1 2.8-1.9 4zm2.3-6H9.7a14.6 14.6 0 0 1 0-4h4.6a14.6 14.6 0 0 1 0 4zm.3 5.6c.6-1.1 1.1-2.3 1.4-3.6h2.9a8 8 0 0 1-4.3 3.6zm1.7-5.6a16 16 0 0 0 0-4h3.4a8 8 0 0 1 0 4z"/></svg>
        <span>www.vomra.com.au</span>
      </li>
      <li>
        <svg viewBox="0 0 24 24"><path d="M3 5h18c.6 0 1 .4 1 1v12c0 .6-.4 1-1 1H3c-.6 0-1-.4-1-1V6c0-.6.4-1 1-1zm1 2.4V17h16V7.4l-8 5.3z M5.2 7L12 11.5 18.8 7z"/></svg>
        <span>admin@vomra.com.au</span>
      </li>
    </ul>

    <p class="address">42-44 Harlow Street Fenwick NSW 2999 Australia</p>
  </section>
</body>
</html>
```